EB-5 Regional Center needs a Web design

Harlow Ridge Financial Partners is an expanding EB-r regional center. We have been successful in sponsoring multiple projects of third-party developers and placing EB-5, B-1, and Private Investments into multiple projects.

We are now partnering directly with project developers in the energy and healthcare to raise foreign capital for projects in those industries. The foreign capital is used as project equity and our collective balance sheets are used to guarantee debt to complete the funding of the projects.

We need a web site where we can post our company credentials, the bios of each partner, a document page for each of our projects where we can post specific project related documents which foreign investors can read, and we will need a section where foreign investors can fill out investor forms confirming that they are qualified investors and leaving their contact so that our agents and executives can make contact.

The final design should reflect the exceptional experience of the partners and our financial strength and stability.

We do have a logo we would want to use on the web design.

Target Market(s)

EB-5 Investors, B-1 Investors, Private Equity and other investors seeking quality investment in job creating US projects.

Coding

Number of Pages Required

5+ page

Font styles to use
Sans Serif

Requirements
Must have
• Pages to display company info, partner bios, projects completed, and a projects in-process page where we can post documents and info on projects for which we are seeking foreign investment. We also need a section where investors can enter their qualifying personal information and leave contact information for us.

```html
<!DOCTYPE html>
<html lang="en">
<head>
<meta charset="utf-8">
<title>Harlow Ridge Financial Partners</title>
<link href="https://fonts.googleapis.com/css2?family=Ubuntu:wght@400;500;700&family=Roboto:wght@400;500;700&display=swap" rel="stylesheet">
<style>
:root{
  --ink:#2f2f2f;
  --text:#3d3d3d;
  --muted:#6b6b6b;
  --white:#ffffff;
  --light:#e7e7e7;
  --mid:#a8a8a8;
  --card:#6a6a6a;
  --dark:#474747;
  --black:#000000;
  --line:#555555;
}
*{box-sizing:border-box;margin:0;padding:0}
html,body{width:1200px;height:3481px;overflow:hidden;background:var(--white)}
body{font-family:"Roboto",sans-serif;color:var(--text);position:relative}
.heading{font-family:"Ubuntu",sans-serif;font-weight:500;color:var(--ink);letter-spacing:.2px}
.rule{position:absolute;height:3px;width:48px;background:var(--line)}

/* header */
.site-header{position:absolute;top:0;left:0;width:1200px;height:103px;background:var(--white)}
.brand{position:absolute;left:58px;top:33px;display:flex;align-items:center;gap:12px}
.brand-mark{width:34px;height:34px;background:var(--mid)}
.brand-name{font-family:"Ubuntu",sans-serif;font-weight:500;font-size:22px;color:#666}
.main-nav{position:absolute;top:40px;left:488px}
.main-nav a{font-size:15px;color:var(--text);text-decoration:none;position:absolute;white-space:nowrap}
.main-nav a.active::after{content:"";position:absolute;left:0;right:0;top:28px;height:2px;background:var(--mid)}

/* hero */
.hero{position:absolute;top:103px;left:0;width:1200px;height:598px;overflow:hidden;
  background:linear-gradient(180deg,#6d6d6d 0%,#8e8e8e 35%,#5a5a5a 70%,#3a3a3a 100%)}
.hero-city{position:absolute;inset:0;background:linear-gradient(90deg,rgba(40,40,40,.5) 0%,rgba(0,0,0,0) 30%,rgba(230,230,230,.25) 85%,rgba(60,60,60,.3) 100%)}
.hero-diamond{position:absolute;left:68px;top:65px}
.hero-copy{position:absolute;left:68px;width:480px;text-align:center;color:var(--white)}
.hero-kicker{top:228px;font-family:"Ubuntu",sans-serif;font-weight:500;font-size:26px}
.hero-title{top:258px;font-family:"Ubuntu",sans-serif;font-weight:700;font-size:46px}
.hero-sub{top:325px;font-size:15px;line-height:20px;padding:0 90px}
.hero-btn{position:absolute;left:216px;top:386px;width:180px;height:52px;border-radius:26px;background:var(--mid);
  color:var(--white);font-weight:700;font-size:16px;display:flex;align-items:center;justify-content:center}
.hero-dots{position:absolute;left:1114px;top:235px}
.hero-dots span{display:block;width:13px;height:13px;border-radius:50%;background:var(--white);margin-bottom:8.5px}
.hero-dots span.current{background:transparent;border:2px solid var(--white)}

/* about */
.about{position:absolute;top:701px;left:0;width:1200px;height:546px;background:var(--white)}
.about h2{position:absolute;left:162px;top:120px;font-size:34px}
.about .rule{left:162px;top:172px;width:30px;height:2px}
.about p{position:absolute;left:162px;width:460px;font-size:16px;line-height:26px;color:var(--text)}
.btn-outline{position:absolute;border:2px solid var(--text);border-radius:30px;color:var(--text);font-weight:500;
  display:flex;align-items:center;justify-content:center;background:transparent}
.about-visual{position:absolute;left:653px;top:76px;width:418px;height:412px;border-radius:6px;
  background:linear-gradient(180deg,#8fbf5a 0%,#6e9c3f 40%,#b48866 75%,#e4d4c7 100%)}

/* projects */
.projects{position:absolute;top:1247px;left:0;width:1200px;height:555px;
  background:linear-gradient(180deg,#4d4d4d 0%,#5a5a5a 40%,#4a4a4a 100%)}
.projects h2{position:absolute;left:0;width:1200px;text-align:center;top:58px;font-size:34px;color:var(--white)}
.projects .rule{left:578px;top:104px;background:#bdbdbd;height:2px}
.project-card{position:absolute;top:149px;width:322px;height:315px}
.project-photo{position:absolute;left:0;top:0;width:322px;height:225px;
  background:linear-gradient(160deg,#8aa8c9 0%,#2f5378 50%,#0f1f35 100%)}
.project-caption{position:absolute;left:16px;top:187px;width:294px;height:127px;background:var(--card);
  text-align:center;color:var(--white)}
.project-caption h3{font-family:"Ubuntu",sans-serif;font-weight:500;font-size:19px;margin-top:26px}
.project-caption p{font-size:13px;line-height:20px;margin-top:10px;color:#e8e8e8;padding:0 28px}

/* partners */
.partners{position:absolute;top:1802px;left:0;width:1200px;height:481px;background:var(--light)}
.partners h2{position:absolute;left:0;width:1190px;text-align:center;top:60px;font-size:32px}
.partners .rule{left:565px;top:107px;height:2px}
.slider-arrow{position:absolute;top:245px}
.partner-photo{position:absolute;width:187px;height:202px;border:1px solid #9a9a9a;background:var(--light)}
.partner-photo div{position:absolute;left:10px;top:10px;right:10px;bottom:10px;
  background:linear-gradient(180deg,#d6d6d6 0%,#8d8d8d 100%)}
.partner-name{position:absolute;font-family:"Ubuntu",sans-serif;font-weight:500;font-size:19px;color:var(--ink)}
.partner-bio{position:absolute;width:245px;font-size:12.5px;line-height:20.5px;color:var(--muted)}
.partners .btn-outline{width:135px;height:42px;font-size:12.5px;border-color:#555}

/* testimonials */
.testimonials{position:absolute;top:2283px;left:0;width:1200px;height:492px;background:var(--white);text-align:center}
.testimonials h2{position:absolute;left:0;width:1210px;top:70px;font-size:31px}
.testimonials .rule{left:578px;top:116px;height:2px}
.quote-mark{position:absolute;left:0;width:1206px;top:140px;font-family:"Ubuntu",sans-serif;font-weight:700;font-size:96px;color:#777;line-height:96px;height:60px;overflow:hidden}
.quote-text{position:absolute;left:240px;width:722px;top:204px;font-size:18px;line-height:31px;color:#5a5a5a}
.quote-author{position:absolute;left:0;width:1198px;top:312px;font-weight:700;font-size:16px;color:var(--muted);letter-spacing:.3px}
.circle-arrow{position:absolute;top:215px;width:46px;height:46px;border-radius:50%;background:var(--dark)}
.btn-solid{position:absolute;background:var(--black);color:var(--white);font-weight:700;border-radius:28px;
  display:flex;align-items:center;justify-content:center}

/* contact */
.contact{position:absolute;top:2775px;left:0;width:1200px;height:516px;overflow:hidden;
  background:linear-gradient(90deg,#5d5d5d 0%,#8a8a8a 25%,#b5b5b5 45%,#e4e4e4 65%,#f4f4f4 100%)}
.contact-city{position:absolute;inset:0;
  background:linear-gradient(180deg,rgba(235,235,235,.45) 0%,rgba(255,255,255,0) 35%,rgba(60,60,60,.18) 100%)}
.contact h2{position:absolute;left:577px;top:88px;font-size:30px;font-weight:700;color:var(--ink)}
.contact .rule{left:577px;top:126px;width:52px;height:3px;background:var(--ink)}
.field{position:absolute;background:var(--white);border:1px solid #d2d2d2;font-size:12px;color:#444;padding:16px 0 0 24px}
.contact .btn-solid{left:577px;top:393px;width:173px;height:50px;font-size:19px;font-family:"Ubuntu",sans-serif}

/* footer */
.site-footer{position:absolute;top:3291px;left:0;width:1200px;height:190px;background:var(--black);color:var(--white)}
.footer-nav{position:absolute;top:53px;left:0;width:1200px;text-align:center;font-size:15px}
.footer-nav span{margin:0 19px}
.copyright{position:absolute;top:87px;left:0;width:1200px;text-align:center;font-size:13px;color:#bdbdbd}
.social{position:absolute;top:128px;left:535px;display:flex;gap:30px}
.social span{width:20px;height:20px;border-radius:50%;background:var(--white)}
</style>
</head>
<body>

<header class="site-header">
  <div class="brand">
    <div class="brand-mark"></div>
    <div class="brand-name">Harlow Ridge Financial Partners</div>
  </div>
  <nav class="main-nav">
    <a class="active" style="left:0">ABOUT US</a>
    <a style="left:115px">SERVICES</a>
    <a style="left:224px">OUR PARTNERS</a>
    <a style="left:375px">PROJECTS</a>
    <a style="left:486px">NEWS</a>
    <a style="left:571px">CONTACT US</a>
  </nav>
</header>

<section class="hero">
  <div class="hero-city" role="img" aria-label="Black and white aerial view of a downtown city skyline"></div>
  <svg class="hero-diamond" width="480" height="470" viewBox="0 0 480 470">
    <polygon points="240,0 480,300 240,470 0,300" fill="#8a8a8a" fill-opacity=".82"/>
    <polygon points="240,0 480,300 240,470" fill="#6f6f6f" fill-opacity=".35"/>
  </svg>
  <div class="hero-copy hero-kicker">WELCOME TO</div>
  <div class="hero-copy hero-title">HARLOW RIDGE</div>
  <div class="hero-copy hero-sub">Harlow Ridge Financial Partners is an expanding EB-r regional center.</div>
  <div class="hero-btn">LEARN MORE</div>
  <div class="hero-dots"><span class="current"></span><span></span><span></span><span></span></div>
</section>

<section class="about">
  <h2 class="heading">ABOUT HARLOW RIDGE</h2>
  <div class="rule"></div>
  <p style="top:194px">Harlow Ridge Financial Partners is an expanding EB-r regional center. We have been successful in sponsoring multiple projects of third-party developers and placing EB-5, B-1, and Private Investments into multiple projects.</p>
  <p style="top:309px">Augiat in pede Fusce tellus Sed metus augue convallis et vehicula ut pulvinar eu ante Integer orci tellus</p>
  <div class="btn-outline" style="left:157px;top:389px;width:183px;height:56px;font-size:16px">LEARN MORE</div>
  <div class="about-visual" role="img" aria-label="Young green plants growing from stacks of coins"></div>
</section>

<section class="projects">
  <h2 class="heading">OUR PROJECTS</h2>
  <div class="rule"></div>
  <div class="project-card" style="left:97px">
    <div class="project-photo" role="img" aria-label="Office towers lit at dusk"></div>
    <div class="project-caption"><h3>PROJECT TITLE</h3><p>Augiat in pede Fusce tellus Sed metus augue convallis et vehicula ut</p></div>
  </div>
  <div class="project-card" style="left:442px">
    <div class="project-photo" role="img" aria-label="Blue glass skyscraper facades"></div>
    <div class="project-caption"><h3>PROJECT TITLE</h3><p>Augiat in pede Fusce tellus Sed metus augue convallis et vehicula ut</p></div>
  </div>
  <div class="project-card" style="left:786px">
    <div class="project-photo" role="img" aria-label="Modern towers against a cloudy sky"></div>
    <div class="project-caption"><h3>PROJECT TITLE</h3><p>Augiat in pede Fusce tellus Sed metus augue convallis et vehicula ut</p></div>
  </div>
</section>

<section class="partners">
  <h2 class="heading">PARTNER BIOS</h2>
  <div class="rule"></div>
  <svg class="slider-arrow" style="left:66px" width="22" height="40" viewBox="0 0 22 40"><polyline points="18,4 4,20 18,36" fill="none" stroke="#666" stroke-width="4"/></svg>
  <svg class="slider-arrow" style="left:1150px" width="22" height="40" viewBox="0 0 22 40"><polyline points="4,4 18,20 4,36" fill="none" stroke="#666" stroke-width="4"/></svg>

  <div class="partner-photo" style="left:139px;top:173px"><div role="img" aria-label="Portrait photo of partner Dorian Vale"></div></div>
  <div class="partner-name" style="left:359px;top:175px">DORIAN VALE</div>
  <div class="partner-bio" style="left:359px;top:216px">Augiat in pede Fusce tellus Sed metus augue convallis et vehicula ut pulvinar eu ante Integer orci tellus tristique vitae consequat nec mauris viverra in gravida eu mattis in ante Morbi eget arcurm</div>
  <div class="btn-outline" style="left:357px;top:330px">LEARN MORE</div>

  <div class="partner-photo" style="left:635px;top:164px"><div role="img" aria-label="Portrait photo of partner Mira Castell"></div></div>
  <div class="partner-name" style="left:855px;top:166px">MIRA CASTELL</div>
  <div class="partner-bio" style="left:855px;top:207px">Augiat in pede Fusce tellus Sed metus augue convallis et vehicula ut pulvinar eu ante Integer orci tellus tristique vitae consequat nec mauris viverra in gravida eu mattis in ante Morbi eget arcurm</div>
  <div class="btn-outline" style="left:853px;top:320px">LEARN MORE</div>
</section>

<section class="testimonials">
  <h2 class="heading">WHAT OUR CLIENT SAYS</h2>
  <div class="rule"></div>
  <div class="quote-mark">&ldquo;</div>
  <div class="circle-arrow" style="left:142px"><svg width="46" height="46" viewBox="0 0 46 46"><polyline points="26,15 18,23 26,31" fill="none" stroke="#fff" stroke-width="2.5"/></svg></div>
  <div class="circle-arrow" style="left:1021px"><svg width="46" height="46" viewBox="0 0 46 46"><polyline points="20,15 28,23 20,31" fill="none" stroke="#fff" stroke-width="2.5"/></svg></div>
  <p class="quote-text">Nunc tempus felis vitae urna Vivamus porttitor neque at volutpat rutrum purus nisi eleifend libero a tempus libero lectus feugiat felis Morbi diam mauris viverra in gravida eu mattis in anquam Curabitur vel dolor ultrices ipsum dictum</p>
  <div class="quote-author">DORIAN VALE</div>
  <div class="btn-solid" style="left:492px;top:370px;width:220px;height:53px;font-size:15px">VIEW MORE STORIES</div>
</section>

<section class="contact">
  <div class="contact-city" role="img" aria-label="Black and white aerial view of a dense city skyline"></div>
  <h2 class="heading">CONTACT FORM</h2>
  <div class="rule"></div>
  <div class="field" style="left:577px;top:153px;width:266px;height:48px">Name:</div>
  <div class="field" style="left:855px;top:153px;width:266px;height:48px">Phone:</div>
  <div class="field" style="left:577px;top:215px;width:266px;height:48px">Email:</div>
  <div class="field" style="left:855px;top:215px;width:266px;height:48px">Subject:</div>
  <div class="field" style="left:577px;top:277px;width:544px;height:97px">Message:</div>
  <div class="btn-solid">SUBMIT</div>
</section>

<footer class="site-footer">
  <div class="footer-nav"><span>ABOUT US</span><span>SERVICES</span><span>OUR PARTNERS</span><span>PROJECTS</span><span>NEWS</span><span>CONTACT US</span></div>
  <div class="copyright">&copy; 2020 Company Name | All Rights Reserved</div>
  <div class="social">
    <span role="img" aria-label="Social profile link"></span>
    <span role="img" aria-label="Social profile link"></span>
    <span role="img" aria-label="Social profile link"></span>
  </div>
</footer>

</body>
</html>
```